Northvale Strategy Partners Website Design

I need a website design for my new business consulting and executive coaching firm, Northvale Strategy Partners. We provide consultative services to business C-suites as well as personal coaching to executives. I have attached the logo with color scheme I have chosen. I would like the website to reflect professionalism and continue the color scheme in the logo.

Target Market(s)

Small to medium business and their executives; middle to upper income men and women in mid- to late career looking for significance

Industry/Entity Type

Business Consultant

Number of Pages Required

4 page

Requirements
Must have
• A homepage with prominent logo and way to contact for more information; an area on the homepage with easy to read, clear text to describe what the company does; a prominent area on the homepage for a tagline; a blog page that can be updated regularly, an "about us" page with biographical information; an "about us" page; a page detailing services offered
• The web design must match the logo colors and font that I have uploaded.
Nice to have
• A lighthouse picture in the background or header
Should not have
• A lot of text area on the homepage

```html
<!DOCTYPE html>
<html lang="en">
<head>
<meta charset="utf-8">
<title>Northvale Strategy Partners</title>
<link href="https://fonts.googleapis.com/css2?family=Montserrat:wght@400;500;600&family=Open+Sans:wght@400;600&family=Roboto+Slab:wght@400;500&display=swap" rel="stylesheet">
<style>
:root{
  --maroon:#7a1013;
  --navy:#1f2b5e;
  --ink:#1d1d1d;
  --grey-text:#6b6b6b;
  --panel:#efefef;
  --white:#ffffff;
  --dark:#212121;
  --darker:#111111;
  --line:#e2e2e2;
}
*{box-sizing:border-box;margin:0;padding:0}
html,body{width:1200px;height:2711px;overflow:hidden}
body{position:relative;background:var(--white);font-family:"Open Sans",Arial,sans-serif;color:var(--ink)}
section,header,nav,footer{position:absolute;left:0;width:1200px}
.slab{font-family:"Roboto Slab",Georgia,serif}
.mont{font-family:"Montserrat",Arial,sans-serif}

/* top bar */
.top-bar{top:0;height:52px;background:var(--white);border-bottom:1px solid var(--line)}
.top-menu{position:absolute;left:86px;top:0;display:flex;height:52px}
.top-menu a{font-family:"Montserrat",Arial,sans-serif;font-size:14px;color:#222;text-decoration:none;padding:0 22px;line-height:52px;border-right:1px solid var(--line)}
.top-menu a.active{color:var(--maroon)}
.social{position:absolute;right:78px;top:9px;display:flex;gap:6px}
.social span{width:34px;height:34px;background:#2a2a2a;display:block}
.social span:first-child{background:var(--maroon)}

/* header */
.site-header{top:52px;height:141px;background:var(--white)}
.brand{position:absolute;left:80px;top:44px;display:flex;align-items:center;gap:12px;font-family:"Roboto Slab",Georgia,serif;font-size:21px;color:var(--navy);font-weight:500;line-height:1.15;width:240px}
.brand i{width:16px;height:16px;background:var(--maroon);flex:none}
.contact{position:absolute;top:48px;display:flex;align-items:center;gap:14px}
.contact small{display:block;font-family:"Montserrat",Arial,sans-serif;font-size:11px;color:#555}
.contact b{display:block;font-family:"Montserrat",Arial,sans-serif;font-size:17px;font-weight:500;color:#111}
.contact.phone{left:732px}
.contact.mail{left:912px;padding-left:24px;border-left:1px solid #ccc;height:48px;top:44px}

/* hero */
.hero{top:193px;height:521px;background:linear-gradient(100deg,#3a3a3f 0%,#8ea2a8 30%,#cfe1e1 50%,#9aaab0 70%,#2c2d33 100%)}
.hero-dots{position:absolute;left:562px;bottom:30px;display:flex;gap:8px}
.hero-dots span{width:14px;height:14px;border-radius:50%;border:2px solid #333}
.hero-dots span.on{background:var(--navy);border-color:var(--navy)}

/* services */
.services{top:714px;height:417px;background:var(--panel)}
.services h2{position:absolute;right:582px;top:60px;font-family:"Roboto Slab",Georgia,serif;font-weight:400;font-size:31px;letter-spacing:3px;color:var(--maroon)}
.services h3{position:absolute;right:582px;top:136px;font-family:"Montserrat",Arial,sans-serif;font-weight:500;font-size:18px}
.services p{position:absolute;right:582px;top:183px;width:500px;text-align:right;font-size:13.5px;line-height:25px;color:var(--grey-text)}
.btn{display:block;background:var(--maroon);color:var(--white);text-align:center;font-family:"Montserrat",Arial,sans-serif;font-size:19px;text-decoration:none}
.services .btn{position:absolute;left:431px;top:293px;width:188px;height:51px;line-height:51px}
.services-photo{position:absolute;left:658px;top:81px;width:394px;height:259px;border:1px solid #999;background:linear-gradient(120deg,#d8e4ea 0%,#8a98a2 40%,#2c2f36 65%,#50555c 100%)}

/* about */
.about{top:1131px;height:371px;background:var(--white);text-align:center}
.about h2{margin-top:68px;font-family:"Roboto Slab",Georgia,serif;font-weight:400;font-size:31px;letter-spacing:3px;color:var(--maroon)}
.about p{width:820px;margin:18px auto 0;font-size:16.5px;line-height:29px;color:#222}
.about .btn{width:186px;height:51px;line-height:51px;margin:42px auto 0;font-family:"Roboto Slab",Georgia,serif;font-size:18px}

/* testimonials */
.testimonials{top:1502px;height:415px;background:linear-gradient(90deg,#2a2e36 0%,#20252e 40%,#2e2c2a 75%,#5a4428 100%);text-align:center;color:var(--white)}
.testimonials h2{margin-top:56px;font-family:"Roboto Slab",Georgia,serif;font-weight:400;font-size:31px;letter-spacing:3px}
.testimonials p{width:680px;margin:24px auto 0;font-size:13.5px;line-height:23px}
.person{position:absolute;left:488px;top:230px;display:flex;align-items:center;gap:20px;text-align:left}
.avatar{width:88px;height:88px;border-radius:50%;border:3px solid #ddd;background:linear-gradient(#9c7a63,#f1f1f1)}
.person b{display:block;font-family:"Roboto Slab",Georgia,serif;font-size:20px;font-weight:500}
.person small{font-family:"Roboto Slab",Georgia,serif;font-size:14px}
.t-dots{position:absolute;left:540px;top:372px}

/* blog */
.blog{top:1917px;height:282px;background:var(--panel)}
.blog h2{text-align:center;margin-top:55px;font-family:"Roboto Slab",Georgia,serif;font-weight:400;font-size:31px;letter-spacing:3px;color:var(--maroon)}
.post{position:absolute;top:129px;display:flex;gap:14px}
.date{width:60px;flex:none;text-align:center;color:var(--white)}
.date .d{display:block;background:var(--navy);height:60px;line-height:60px;font-size:34px}
.date .m{display:block;background:var(--maroon);height:30px;line-height:30px;font-size:18px}
.post h3{font-family:"Montserrat",Arial,sans-serif;font-weight:500;font-size:19px;margin-top:4px}
.post p{font-size:14.5px;line-height:26px;color:var(--grey-text);margin-top:4px}
.post p em{color:var(--maroon);font-style:normal;font-weight:600}

/* contact form */
.touch{top:2199px;height:457px;background:var(--dark);color:var(--white)}
.touch h2{text-align:center;margin-top:44px;font-family:"Roboto Slab",Georgia,serif;font-weight:400;font-size:31px;letter-spacing:3px}
.field{position:absolute;border:1px solid #3a3a3a;background:#1e1e1e;border-radius:20px;font-size:12px;color:#8a8a8a;padding:10px 20px}
.field.name{left:258px;top:116px;width:338px;height:40px}
.field.email{left:602px;top:116px;width:338px;height:40px}
.field.msg{left:258px;top:165px;width:682px;height:101px;border-radius:14px}
.touch .submit{position:absolute;left:506px;top:280px;width:186px;height:51px;line-height:51px;background:var(--white);color:#111;font-family:"Roboto Slab",Georgia,serif;font-size:19px}
.footer-nav{position:absolute;left:76px;top:374px;width:1048px;border-top:1px solid #3a3a3a;display:flex;justify-content:center;gap:42px;padding-top:30px}
.footer-nav a{font-family:"Open Sans",Arial,sans-serif;font-size:14px;color:#8a8a8a;text-decoration:none}
.footer-nav a.active{color:var(--white);text-decoration:underline}

/* bottom */
.bottom-bar{top:2656px;height:55px;background:var(--darker)}
.copy{position:absolute;left:80px;top:19px;font-size:11.5px;color:#ccc}
.copy span{color:var(--maroon)}
.foot-social{position:absolute;right:78px;top:19px;display:flex;gap:26px}
.foot-social span{width:14px;height:14px;background:#ddd;display:block}
.foot-social span:first-child{background:var(--maroon)}
</style>
</head>
<body>

<nav class="top-bar">
  <div class="top-menu">
    <a class="active" href="#">HOME</a><a href="#">ABOUT US</a><a href="#">SERVICES</a><a href="#">TESTIMONIAL</a><a href="#">BLOG</a><a href="#">CONTACT US</a>
  </div>
  <div class="social" aria-label="Social links"><span></span><span></span><span></span><span></span></div>
</nav>

<header class="site-header">
  <div class="brand"><i></i>Northvale Strategy Partners</div>
  <div class="contact phone">
    <svg width="22" height="36" viewBox="0 0 22 36"><rect x="1" y="1" width="20" height="34" rx="4" fill="var(--maroon)"/><rect x="4" y="6" width="14" height="21" fill="#fff"/><circle cx="11" cy="31" r="2" fill="#fff"/></svg>
    <div><small>Call Us Today</small><b>+1234567890</b></div>
  </div>
  <div class="contact mail">
    <svg width="40" height="30" viewBox="0 0 40 30"><rect width="40" height="30" rx="3" fill="var(--maroon)"/><path d="M2 3 L20 17 L38 3" stroke="#fff" stroke-width="2.5" fill="none"/></svg>
    <div><small>Mail Us Today</small><b>xyz@example.com</b></div>
  </div>
</header>

<section class="hero" role="img" aria-label="Photo of a smiling business team seated at a glass meeting table with a video-call monitor">
  <div class="hero-dots"><span></span><span class="on"></span><span></span></div>
</section>

<section class="services">
  <h2>Our Services</h2>
  <h3>Consultative Services</h3>
  <p>Lorem ipsum dolor sit amet, consectetur adipiscing elit, sed do eiusmod tempor incididunt ut labore et dolore magna aliqua. Ut enim ad minim veniam, quis nostrud exercitation</p>
  <a class="btn" href="#">View All</a>
  <div class="services-photo" role="img" aria-label="Photo of two businessmen in a consultation across a meeting table"></div>
</section>

<section class="about">
  <h2>Know ABout Us</h2>
  <p>Lorem ipsum dolor sit amet, consectetur adipiscing elit, sed do eiusmod tempor incididunt ut labore et dolore magna aliqua. Ut enim ad minim veniam, quis nostrud exercitation ullamco laboris nisi ut aliquip ex ea commodo consequat. Duis aute irure dolor in reprehenderit.</p>
  <a class="btn" href="#">READ MORE</a>
</section>

<section class="testimonials" role="img" aria-label="Background photo of a lighthouse beaming under a stormy evening sky">
  <h2>Testimonials</h2>
  <p>Lorem ipsum dolor sit amet, consectetur adipiscing elit, sed do eiusmod tempor incididunt ut labore et dolore magna aliqua. Ut enim ad minim veniam, quis nostrud exercitation ullamco laboris nisi ut aliquip ex ea commodo consequat. Duis aute irure dolor in reprehenderit.</p>
  <div class="person">
    <div class="avatar" role="img" aria-label="Portrait photo of the client"></div>
    <div><b>-Name Here</b><small>Designation here</small></div>
  </div>
  <svg class="t-dots" width="120" height="14" viewBox="0 0 120 14" fill="#000">
    <path d="M0 12 L6 2 L12 12Z"/><path d="M22 2 L34 2 L28 12Z" fill="#fff"/><path d="M44 12 L50 2 L56 12Z"/><path d="M66 12 L72 2 L78 12Z"/><path d="M88 12 L94 2 L100 12Z"/><path d="M108 12 L114 2 L120 12Z"/>
  </svg>
</section>

<section class="blog">
  <h2>Our Latest Blog</h2>
  <article class="post" style="left:94px"><div class="date"><span class="d">29</span><span class="m">Dec</span></div><div><h3>Lorem Ipsume dolor</h3><p>Lorem ipsum dolor sit amet,<br>consectetur adipiscing elit....<em>»</em></p></div></article>
  <article class="post" style="left:479px"><div class="date"><span class="d">29</span><span class="m">Dec</span></div><div><h3>Lorem Ipsume dolor</h3><p>Lorem ipsum dolor sit amet,<br>consectetur adipiscing elit....<em>»</em></p></div></article>
  <article class="post" style="left:833px"><div class="date"><span class="d">29</span><span class="m">Dec</span></div><div><h3>Lorem Ipsume dolor</h3><p>Lorem ipsum dolor sit amet,<br>consectetur adipiscing elit....<em>»</em></p></div></article>
</section>

<section class="touch">
  <h2>Keep In Touch</h2>
  <div class="field name">Name</div>
  <div class="field email">Email Id</div>
  <div class="field msg">Message</div>
  <div class="submit" style="text-align:center">SUBMIT</div>
  <div class="footer-nav">
    <a class="active" href="#">HOME</a><a href="#">ABOUT US</a><a href="#">SERVICES</a><a href="#">TESTIMONIAL</a><a href="#">BLOG</a><a href="#">CONTACT US</a>
  </div>
</section>

<footer class="bottom-bar">
  <div class="copy">© <span>NORTHVALE STRATEGY PARTNERS</span> - 2015. All Rights Reserved</div>
  <div class="foot-social"><span></span><span></span><span></span><span></span></div>
</footer>

</body>
</html>
```